Tandem Hearth Works Pty Ltd

We need business cards for a company based in Perth, we install, service and maintain fire equipment.
On the front we want a great design with our logo and a small spot for our full company name, general company email address and office number. On the back we need space for our name, title, mobile number and email address on the back.

Target Market(s)

Facility managers and commercial/industrial building owners/occupiers.

Contact Information for Business Card

Font styles to use
Sans Serif

Requirements
Must have
• Please only submit 5 of your best samples.
Darker tones are preferred.
Nice to have
• We want to use, black, red and grey. Keep it modern and clean.
I've attached the company logo and a sample of a boarder we use on our emergency plans.
Should not have
• No preference. Let the designer choose.

```html
<!DOCTYPE html>
<html lang="en">
<head>
<meta charset="utf-8">
<title>Tandem Hearth Works Pty Ltd — Business Cards</title>
<link rel="stylesheet" href="https://fonts.googleapis.com/css2?family=Arimo:wght@400;700&display=swap">
<style>
  :root {
    --bg: #2b2b2b;
    --brand-red: #ec1c24;
    --card-white: #ffffff;
    --arc-grey: #9a9aa2;
    --ink-light: #ffffff;
  }
  * { margin: 0; padding: 0; box-sizing: border-box; }
  html, body {
    width: 1200px; height: 1015px; overflow: hidden;
    background: var(--bg);
    font-family: "Arimo", Arial, sans-serif;
  }
  .canvas {
    position: relative; width: 1200px; height: 1015px;
    display: flex; flex-direction: column; align-items: center; justify-content: center; gap: 70px;
  }
  .card {
    position: relative; width: 560px; height: 320px; overflow: hidden;
    background: var(--brand-red); color: var(--ink-light);
    box-shadow: 0 12px 30px rgba(0,0,0,.45);
  }
  /* Company side */
  .card--company {
    display: flex; flex-direction: column; align-items: center; justify-content: center; text-align: center;
  }
  .company-name {
    font-weight: 700; font-size: 24px; line-height: 1.12; text-transform: uppercase; letter-spacing: .5px;
  }
  .company-phone {
    font-weight: 700; font-size: 30px; margin-top: 12px; letter-spacing: .5px;
  }
  .company-links {
    display: flex; gap: 26px; margin-top: 14px; font-size: 15px;
  }
  .contact-item { display: flex; align-items: center; gap: 8px; }
  .icon { width: 18px; height: 18px; flex: none; }
  /* Personal side */
  .card__backdrop { position: absolute; inset: 0; }
  .brand-name {
    position: absolute; left: 300px; top: 86px; width: 230px;
    color: var(--brand-red); font-weight: 700; font-size: 34px; line-height: 1.05; text-transform: uppercase; text-align: center;
  }
  .person {
    position: absolute; left: 36px; top: 150px;
  }
  .person__name { font-weight: 700; font-size: 24px; text-transform: uppercase; letter-spacing: .5px; }
  .person__title { font-size: 17px; margin-top: 2px; }
  .person__contacts { margin-top: 22px; display: flex; flex-direction: column; gap: 6px; font-size: 17px; }
</style>
</head>
<body>
<main class="canvas">

  <section class="card card--company" aria-label="Company side">
    <h1 class="company-name">Tandem Hearth<br>Works Pty Ltd</h1>
    <p class="company-phone">555.0142.0142</p>
    <div class="company-links">
      <span class="contact-item">
        <svg class="icon" viewBox="0 0 20 20" aria-hidden="true"><rect x="1" y="4" width="18" height="12" fill="none" stroke="#fff" stroke-width="1.8"/><path d="M1 4l9 7 9-7" fill="none" stroke="#fff" stroke-width="1.8"/></svg>
        info@tandemhearth.com
      </span>
      <span class="contact-item">
        <svg class="icon" viewBox="0 0 20 20" aria-hidden="true"><circle cx="10" cy="10" r="8" fill="none" stroke="#fff" stroke-width="1.6"/><ellipse cx="10" cy="10" rx="3.5" ry="8" fill="none" stroke="#fff" stroke-width="1.4"/><path d="M2 10h16M3.5 6h13M3.5 14h13" stroke="#fff" stroke-width="1.2"/></svg>
        www.tandemhearth.com
      </span>
    </div>
  </section>

  <section class="card card--personal" aria-label="Personal side">
    <svg class="card__backdrop" viewBox="0 0 560 320" aria-hidden="true">
      <rect width="560" height="320" fill="var(--brand-red)"/>
      <circle cx="490" cy="116" r="220" fill="var(--arc-grey)"/>
      <circle cx="490" cy="116" r="217" fill="var(--brand-red)"/>
      <circle cx="500" cy="110" r="220" fill="var(--card-white)"/>
    </svg>
    <p class="brand-name">Tandem<br>Hearth</p>
    <div class="person">
      <h2 class="person__name">Marcus Hale</h2>
      <p class="person__title">Managing Director</p>
      <div class="person__contacts">
        <span class="contact-item">
          <svg class="icon" viewBox="0 0 20 20" aria-hidden="true"><rect x="5" y="1.5" width="10" height="17" rx="2" fill="none" stroke="#fff" stroke-width="1.8"/><circle cx="10" cy="15.5" r="1" fill="#fff"/></svg>
          555.0187.0187
        </span>
        <span class="contact-item">
          <svg class="icon" viewBox="0 0 20 20" aria-hidden="true"><rect x="1" y="4" width="18" height="12" fill="none" stroke="#fff" stroke-width="1.8"/><path d="M1 4l9 7 9-7" fill="none" stroke="#fff" stroke-width="1.8"/></svg>
          name@tandemhearth.com
        </span>
      </div>
    </div>
  </section>

</main>
</body>
</html>
```